Smile club flyer design

I am launching an office smile club and would like a design that sits my branding and that is appealing to customers. I have a design (I need a new one) that has all the information.
My website is maplehavendentalcarekx.com
Brand color is green. The design can be any color

Target Market(s)

Ages 30+

Industry/Entity Type

Dental

Font styles to use
Serif

Requirements
Must have
• Appealing to patients

```html
<!DOCTYPE html>
<html lang="en">
<head>
<meta charset="utf-8">
<title>Maplehaven Dental Care – Smile Club Membership</title>
<link href="https://fonts.googleapis.com/css2?family=Anton&family=Barlow+Condensed:wght@400;500&family=Noto+Serif:wght@400;700&family=Poppins:ital,wght@0,600;0,700;1,600&family=Dancing+Script:wght@600&family=Oswald:wght@500&display=swap" rel="stylesheet">
<style>
:root{
  --backdrop:#002a14;
  --green:#067033;
  --green-light:#1fa855;
  --mint:#8affb8;
  --card-bg:#effdf4;
  --yellow:#ffe100;
  --white:#ffffff;
  --ink:#111111;
  --grey:#444444;
}
*{margin:0;padding:0;box-sizing:border-box}
html,body{width:924px;height:1200px;overflow:hidden;background:var(--backdrop)}
.flyer{position:absolute;left:62px;top:0;width:800px;height:1200px;background:linear-gradient(160deg,#fff 55%,#fff 70%,#c9e6d5 100%);overflow:hidden}
.mint-arc{position:absolute;left:401px;top:16px;width:486px;height:486px;border-radius:50%;background:var(--mint)}
.hero-panel{position:absolute;left:0;top:39px;width:466px;height:440px;background:var(--green);border-radius:0 24px 24px 0}
.photo-ring{position:absolute;left:389px;top:38px;width:442px;height:442px;border-radius:50%;background:var(--white)}
.photo-ring svg{position:absolute;left:0;top:0}
.photo{position:absolute;left:419px;top:68px;width:382px;height:382px;border-radius:50%;background:radial-gradient(circle at 65% 40%,#d9b59a 0%,#9a6b52 45%,#3d4d7a 100%)}
.brand{position:absolute;left:0;width:402px;text-align:center;color:var(--white);white-space:nowrap}
.brand-name{top:80px;font:400 46px/1 'Noto Serif',serif}
.brand-sub{top:140px;font:500 17px/1 'Oswald',sans-serif;letter-spacing:6px}
.brand-sub::before,.brand-sub::after{content:"";display:inline-block;width:30px;height:2px;background:var(--white);vertical-align:middle;margin:0 8px}
.intro{position:absolute;left:112px;top:182px;color:var(--yellow);font:600 32px/1 'Dancing Script',cursive;transform:rotate(-3deg)}
.title{position:absolute;left:0;width:374px;text-align:center;color:var(--white);font-family:'Anton',sans-serif;font-weight:400;line-height:1;white-space:nowrap}
.title-1{top:211px;font-size:70px}
.title-2{top:288px;font-size:72px;letter-spacing:-1.5px}
.tagline{position:absolute;left:10px;top:379px;color:var(--yellow);font:500 19px/1 'Barlow Condensed',sans-serif;white-space:nowrap}
.plan{position:absolute;top:544px;width:220px;height:294px;background:var(--card-bg);box-shadow:0 2px 6px rgba(0,0,0,.35);border-bottom:2px solid var(--green)}
.plan svg.head{position:absolute;left:0;top:0}
.plan-name{position:absolute;left:0;top:11px;width:100%;text-align:center;color:var(--yellow);font:700 22px/1 'Noto Serif',serif}
.plan-type{position:absolute;left:0;top:35px;width:100%;text-align:center;color:var(--white);font:400 15px/1 'Noto Serif',serif}
.price{position:absolute;left:74px;top:61px;width:72px;height:72px;border-radius:50%;background:var(--green);border:4px solid var(--white);color:var(--white);text-align:center}
.price b{display:block;font:400 30px/1 'Anton',sans-serif;margin-top:6px}
.price i{display:block;font:normal 500 12px/1 'Barlow Condensed',sans-serif}
.features{position:absolute;left:16px;top:152px;right:6px;list-style:none}
.features li{position:relative;padding-left:21px;margin-bottom:9px;font:400 14.5px/15px 'Barlow Condensed',sans-serif;color:var(--ink);white-space:nowrap}
.features li svg{position:absolute;left:0;top:3px}
.plan-core{left:53px}.plan-bright{left:290px}.plan-total{left:527px}
.refresh{left:490px;top:890px;height:268px;width:259px}
.refresh .plan-name{top:17px;font-size:23px}
.refresh .plan-type{top:42px;font-size:19px}
.refresh .price{left:87px;top:72px;width:84px;height:84px}
.refresh .price b{font-size:33px;margin-top:18px}
.refresh .features{top:182px;left:20px}
.refresh .features li{font-size:15.5px;line-height:17px;margin-bottom:10px}
.new-tag{position:absolute;left:2px;top:16px;color:var(--white);font:400 13px/1 'Noto Serif',serif;transform:rotate(-45deg)}
.finance{position:absolute;left:20px;width:450px;text-align:center;white-space:nowrap}
.finance-head{top:900px;font:700 17px/1 'Poppins',sans-serif;color:var(--ink)}
.partners{top:930px;display:flex;justify-content:center;gap:28px;font:700 28px/1 'Poppins',sans-serif}
.partner{display:flex;align-items:center;gap:6px;color:#2b6b50}
.partner-mark{width:16px;height:16px;border-radius:50%;background:#2b6b50}
.partner-b{color:#333}
.partner-b .partner-mark{background:#333}
.plans-note{top:971px;font:600 14px/1 'Poppins',sans-serif;letter-spacing:1px;color:var(--grey)}
.fee{top:998px;font:italic 600 15px/1 'Poppins',sans-serif;color:var(--grey)}
.join{top:1030px;font:400 47px/1 'Anton',sans-serif;letter-spacing:-0.5px;color:var(--green)}
.phone{top:1088px;font:400 53px/1 'Anton',sans-serif;color:#000}
</style>
</head>
<body>
<div class="flyer">
  <div class="mint-arc"></div>
  <div class="hero-panel"></div>
  <div class="photo-ring">
    <svg width="442" height="442" viewBox="0 0 442 442">
      <circle cx="221" cy="221" r="206" fill="none" stroke="var(--green)" stroke-width="3"/>
      <path d="M140 30 A206 206 0 0 1 430 160" fill="none" stroke="var(--green)" stroke-width="10" stroke-linecap="round"/>
      <path d="M140 414 A206 206 0 0 0 430 282" fill="none" stroke="var(--green)" stroke-width="10" stroke-linecap="round"/>
      <circle cx="63" cy="98" r="7" fill="var(--green)"/>
      <circle cx="15" cy="221" r="11" fill="var(--green)"/>
      <circle cx="63" cy="344" r="7" fill="var(--green)"/>
    </svg>
  </div>
  <div class="photo" role="img" aria-label="Smiling woman in a dental chair during a check-up with gloved dentist's hands"></div>

  <div class="brand brand-name">Maplehaven</div>
  <div class="brand brand-sub">DENTAL CARE</div>
  <div class="intro">Introducing</div>
  <div class="title title-1">SMILE CLUB</div>
  <div class="title title-2">MEMBERSHIP</div>
  <div class="tagline">AFFORDABLE DENTAL CARE - NO INSURANCE REQUIRED</div>

  <div class="plan plan-core">
    <svg class="head" width="220" height="120" viewBox="0 0 220 120"><path d="M0 0H220V58Q110 150 0 58Z" fill="var(--green)"/><path d="M0 58Q110 150 220 58V66Q110 158 0 66Z" fill="var(--green-light)"/></svg>
    <div class="plan-name">CORE CARE</div>
    <div class="plan-type">Preventive</div>
    <div class="price"><b>$39</b><i>/MONTH</i></div>
    <ul class="features">
      <li><svg width="15" height="9"><ellipse cx="4" cy="5" rx="4" ry="2.5" fill="var(--green-light)"/><ellipse cx="11" cy="5" rx="4" ry="2.5" fill="var(--green)"/></svg>Comprehensive Annual Exam</li>
      <li><svg width="15" height="9"><ellipse cx="4" cy="5" rx="4" ry="2.5" fill="var(--green-light)"/><ellipse cx="11" cy="5" rx="4" ry="2.5" fill="var(--green)"/></svg>2 Professional Cleanings per Year</li>
      <li><svg width="15" height="9"><ellipse cx="4" cy="5" rx="4" ry="2.5" fill="var(--green-light)"/><ellipse cx="11" cy="5" rx="4" ry="2.5" fill="var(--green)"/></svg>Routine Bitewing X-rays</li>
      <li><svg width="15" height="9"><ellipse cx="4" cy="5" rx="4" ry="2.5" fill="var(--green-light)"/><ellipse cx="11" cy="5" rx="4" ry="2.5" fill="var(--green)"/></svg>10% Savings on Treatment</li>
    </ul>
  </div>

  <div class="plan plan-bright">
    <svg class="head" width="220" height="120" viewBox="0 0 220 120"><path d="M0 0H220V58Q110 150 0 58Z" fill="var(--green)"/><path d="M0 58Q110 150 220 58V66Q110 158 0 66Z" fill="var(--green-light)"/></svg>
    <div class="plan-name">BRIGHT</div>
    <div class="plan-type">Cosmetic</div>
    <div class="price"><b>$59</b><i>/MONTH</i></div>
    <ul class="features">
      <li><svg width="15" height="9"><ellipse cx="4" cy="5" rx="4" ry="2.5" fill="var(--green-light)"/><ellipse cx="11" cy="5" rx="4" ry="2.5" fill="var(--green)"/></svg>Annual In-Office Whitening<br>(Top &amp; Bottom)</li>
      <li><svg width="15" height="9"><ellipse cx="4" cy="5" rx="4" ry="2.5" fill="var(--green-light)"/><ellipse cx="11" cy="5" rx="4" ry="2.5" fill="var(--green)"/></svg>Custom Whitening Trays</li>
      <li><svg width="15" height="9"><ellipse cx="4" cy="5" rx="4" ry="2.5" fill="var(--green-light)"/><ellipse cx="11" cy="5" rx="4" ry="2.5" fill="var(--green)"/></svg>15% Savings on Elective Treatment</li>
    </ul>
  </div>

  <div class="plan plan-total">
    <svg class="head" width="220" height="120" viewBox="0 0 220 120"><path d="M0 0H220V58Q110 150 0 58Z" fill="var(--green)"/><path d="M0 58Q110 150 220 58V66Q110 158 0 66Z" fill="var(--green-light)"/></svg>
    <div class="plan-name">TOTAL SMILE</div>
    <div class="plan-type">Periodontal</div>
    <div class="price"><b>$89</b><i>/MONTH</i></div>
    <ul class="features">
      <li><svg width="15" height="9"><ellipse cx="4" cy="5" rx="4" ry="2.5" fill="var(--green-light)"/><ellipse cx="11" cy="5" rx="4" ry="2.5" fill="var(--green)"/></svg>3-4 Perio Maintenance Visits<br>per Year</li>
      <li><svg width="15" height="9"><ellipse cx="4" cy="5" rx="4" ry="2.5" fill="var(--green-light)"/><ellipse cx="11" cy="5" rx="4" ry="2.5" fill="var(--green)"/></svg>1 Comprehensive Exam</li>
      <li><svg width="15" height="9"><ellipse cx="4" cy="5" rx="4" ry="2.5" fill="var(--green-light)"/><ellipse cx="11" cy="5" rx="4" ry="2.5" fill="var(--green)"/></svg>Diagnostic X-rays</li>
      <li><svg width="15" height="9"><ellipse cx="4" cy="5" rx="4" ry="2.5" fill="var(--green-light)"/><ellipse cx="11" cy="5" rx="4" ry="2.5" fill="var(--green)"/></svg>15% Savings on Restorative &amp;<br>Elective Care</li>
    </ul>
  </div>

  <div class="finance finance-head">FLEXIBLE FINANCING FOR TREATMENTS</div>
  <div class="finance partners">
    <span class="partner"><span class="partner-mark"></span>FlexiPay</span>
    <span class="partner partner-b"><span class="partner-mark"></span>Orchard Pay</span>
  </div>
  <div class="finance plans-note">PAYMENT PLANS AVAILABLE</div>
  <div class="finance fee">*$49 Lifetime Activation Fee (Non-refundable)</div>
  <div class="finance join">JOIN SMILE CLUB TODAY!</div>
  <div class="finance phone">865-555-0142</div>

  <div class="plan refresh">
    <svg class="head" width="259" height="140" viewBox="0 0 259 140"><path d="M0 0H259V68Q130 170 0 68Z" fill="var(--green)"/><path d="M0 68Q130 170 259 68V76Q130 178 0 76Z" fill="var(--green-light)"/><path d="M0 0H62L0 62Z" fill="var(--green-light)"/></svg>
    <div class="new-tag">NEW</div>
    <div class="plan-name">SMILE</div>
    <div class="plan-type">Refresh Package</div>
    <div class="price"><b>$499</b></div>
    <ul class="features">
      <li><svg width="15" height="9"><ellipse cx="4" cy="5" rx="4" ry="2.5" fill="var(--green-light)"/><ellipse cx="11" cy="5" rx="4" ry="2.5" fill="var(--green)"/></svg>Cleaning + Comprehensive Exam +<br>Whitening</li>
      <li><svg width="15" height="9"><ellipse cx="4" cy="5" rx="4" ry="2.5" fill="var(--green-light)"/><ellipse cx="11" cy="5" rx="4" ry="2.5" fill="var(--green)"/></svg>Limited Time Offer</li>
    </ul>
  </div>
</div>
</body>
</html>
```